Business card design for web travel company

Hi
we'd like to receive some proposal for a business card design.
Stayvora is a private travel club, dedicated to all travel lovers, with unique offers for exclusive destinations all around the world. At Stayvora you can find a wide range of offers for resorts, boutique hotels and travel packages at the best guaranteed price available on the market. The convenience of the offer is guaranteed by a private sales model: offers are available for a limited time only and they are personally chosen by Stayvora's qualified team of travel experts.
We offer only exclusive hotels with discounted prices but we are not an outlet or a discount supermarket: the design should reflect our connection with luxury, exclusivity using the same style of our website www.stayvora-example.com.
We want to make sure that when we'll present ourself to our business partner they will feel immediately which is our brand positioning giving them also a sense of an affordable and reliable partner.
In attachment you can also find our brand guidelines (please note that we are NOT USING ANY MORE THE TAG LINE "Five star outlet" mentioned in it).
The info to be inserted are:
Name Surname
Job Title
Tel
Mobile (when needed)
Email
Stayvora S.r.l.
Via Bruno Salvi 27
20139 Milano

```html
<!DOCTYPE html>
<html lang="en">
<head>
<meta charset="utf-8">
<title>Stayvora – Business Card</title>
<link rel="stylesheet" href="https://fonts.googleapis.com/css2?family=Exo+2:wght@300;400;700&family=Roboto:wght@400&display=swap">
<style>
  :root {
    --page: #ece8e4;
    --ink: #0a0a0a;
    --band: #141414;
    --paper: #ffffff;
    --gold: #b9a578;
    --muted: #c9c9c9;
  }
  html, body {
    margin: 0;
    width: 1200px;
    height: 900px;
    overflow: hidden;
    background: var(--page);
  }
  .canvas {
    position: relative;
    width: 1200px;
    height: 900px;
  }
  .card {
    position: absolute;
    top: 308px;
    width: 501px;
    height: 286px;
    border-radius: 13px;
    overflow: hidden;
    box-shadow: 0 6px 18px rgba(0, 0, 0, 0.18);
  }
  .texture-fill {
    position: absolute;
    inset: 0;
    background: linear-gradient(120deg, var(--ink) 0%, var(--band) 100%);
  }
  .wordmark {
    position: absolute;
    margin: 0;
    font-family: "Exo 2", sans-serif;
    font-weight: 300;
    font-size: 46px;
    letter-spacing: 0.5px;
    line-height: 1;
  }

  /* Front */
  .card-front { left: 75px; background: var(--paper); }
  .brand-area {
    position: absolute;
    left: 0; top: 0;
    width: 100%; height: 176px;
  }
  .card-front .wordmark {
    right: 18px;
    top: 124px;
    color: var(--ink);
  }
  .gold-rule {
    position: absolute;
    left: 0; top: 176px;
    width: 100%; height: 6px;
    background: var(--gold);
  }
  .contact-band {
    position: absolute;
    left: 0; top: 182px;
    width: 100%; height: 104px;
  }
  .person {
    position: absolute;
    left: 30px; top: 10px;
    margin: 0;
  }
  .person-name {
    margin: 0;
    font-family: "Exo 2", sans-serif;
    font-weight: 700;
    font-size: 20px;
    line-height: 24px;
    color: var(--paper);
  }
  .job-title {
    margin: 0;
    font-family: "Exo 2", sans-serif;
    font-weight: 400;
    font-size: 11px;
    line-height: 14px;
    letter-spacing: 0.6px;
    color: var(--gold);
  }
  .contact-list {
    position: absolute;
    left: 30px; top: 56px;
    margin: 0; padding: 0;
    list-style: none;
    font-family: "Roboto", sans-serif;
    font-size: 12px;
    color: var(--paper);
  }
  .contact-list li {
    display: flex;
    align-items: center;
    gap: 4px;
    height: 18px;
  }
  .contact-list svg { width: 13px; height: 11px; flex: none; }
  .company-address {
    position: absolute;
    right: 22px; top: 50px;
    margin: 0;
    font-family: "Roboto", sans-serif;
    font-style: normal;
    font-size: 11px;
    line-height: 15px;
    text-align: right;
    color: var(--muted);
  }
  .company-address strong {
    font-weight: 400;
    color: var(--paper);
  }

  /* Back */
  .card-back { left: 625px; }
  .card-back .wordmark {
    left: 54px;
    top: 122px;
    color: var(--paper);
  }
  .web-address {
    position: absolute;
    left: 55px; top: 174px;
    margin: 0;
    font-family: "Exo 2", sans-serif;
    font-weight: 400;
    font-size: 12px;
    letter-spacing: 2.2px;
    color: var(--muted);
  }
</style>
</head>
<body>
<main class="canvas">
  <section class="card card-front" aria-label="Business card front">
    <div class="brand-area">
      <p class="wordmark">Stayvora</p>
    </div>
    <div class="gold-rule"></div>
    <div class="contact-band">
      <div class="texture-fill" role="img" aria-label="Dark background with fine diagonal pin-stripe texture"></div>
      <div class="person">
        <h1 class="person-name">Marco Vellani</h1>
        <p class="job-title">Partner Relations Manager</p>
      </div>
      <ul class="contact-list">
        <li>
          <svg viewBox="0 0 13 11" aria-hidden="true">
            <path d="M1 4 Q6.5 0 12 4 L10.5 5.5 L8.8 4.2 L8.8 3 Q6.5 2.2 4.2 3 L4.2 4.2 L2.5 5.5 Z" fill="#b9a578"/>
            <rect x="3" y="5.5" width="7" height="4.5" rx="0.8" fill="#b9a578"/>
          </svg>
          <span>: +23 4567 8910</span>
        </li>
        <li>
          <svg viewBox="0 0 13 11" aria-hidden="true">
            <rect x="1" y="1.5" width="11" height="8" fill="none" stroke="#b9a578" stroke-width="1.1"/>
            <path d="M1 1.5 L6.5 6 L12 1.5" fill="none" stroke="#b9a578" stroke-width="1.1"/>
          </svg>
          <span>: marco@stayvora-example.com</span>
        </li>
      </ul>
      <address class="company-address">
        <strong>Stayvora S.r.l.</strong><br>
        Via Bruno Salvi 27<br>
        20139 Milano
      </address>
    </div>
  </section>

  <section class="card card-back" aria-label="Business card back">
    <div class="texture-fill" role="img" aria-label="Dark background with fine diagonal pin-stripe texture"></div>
    <p class="wordmark">Stayvora</p>
    <p class="web-address">www.stayvora-example.com</p>
  </section>
</main>
</body>
</html>
```